Podcast Cover Art for rebranded podcast - I have inspiration for the designs

I've had a podcast ("Paperboat Radio Hour") since 2018, but I'm in the process of rebranding it. I've attached the old cover art below, which I loved, but I don't need it to look like that at all. The rebranded podcast is called 'Open Window with Marnie Cole.' I've included the show description at the bottom. I've been working on various design options in Canva, but not obsessed with anything yet, but I'm attaching the ones I do like that I think just need some refining. My very favorite is the one labeled 'favorite_Open Window' so I wouldn't mind keeping that general idea but perfected by a designer. Ultimately, I want something cool, fairly clean, modern, eye catching. I'm into neutrals with maybe a pop of color, so think black, white, grey..maybe silver, and I love a pop of red..and I'm not opposed to other options for the pop color. The show is going to be inspiring, entertaining, and funny. Oh and one other idea I had but I'm not sure if it makes sense with the title and/or what the show is about..but a vinyl record with Open Window with Marnie Cole on it somehow, on a record player..not sure.

Ever wonder what it means to truly live authentically? Curious about how to embrace the unpredictability of life? Ready for some heartfelt and lighthearted conversations that inspire and entertain?
Join Marnie Cole as she dives into the raw, real, and unscripted moments of life. In each episode, Marnie brings candid conversations and genuine insights into the ups and downs we all experience. From personal growth and self-discovery to inspiring stories and valuable life lessons, "Open Window" is a space where authenticity reigns and spontaneity is celebrated.
Whether she's sharing her own journey or chatting with inspiring guests, Marnie invites you to explore the beauty of living life without a script. Expect honest reflections, thought-provoking discussions, and a refreshing perspective on navigating life's unpredictable path—all with a dash of fun and humor to keep things lively and entertaining. Step into the unscripted moments of life and tune in for a blend of depth and lightheartedness that will leave you inspired, smiling, and most importantly laughing.

Target Market(s)

25-50 year old women and men (primarily women)

Font styles to use
Sans Serif

Requirements
Should not have
• nothing too feminine or girly, nothing cheesy :)

```html
<!DOCTYPE html>
<html lang="en">
<head>
<meta charset="utf-8">
<title>Open Window with Marnie Cole — Podcast Cover</title>
<link rel="stylesheet" href="https://fonts.googleapis.com/css2?family=Abril+Fatface&family=Mrs+Saint+Delafield&family=Oswald:wght@700&display=swap">
<style>
  :root {
    --ink: #000000;
    --paper: #ffffff;
    --accent-red: #d9121b;
    --silver-light: #f4f4f4;
    --silver-mid: #9a9a9a;
    --silver-dark: #6e6e6e;
    --glow: #3a3a3a;
    --portrait-base: #5a6a55;
  }
  html, body {
    margin: 0;
    padding: 0;
    width: 1200px;
    height: 1200px;
    overflow: hidden;
    background: var(--paper);
  }
  .cover {
    position: relative;
    width: 1200px;
    height: 1200px;
    overflow: hidden;
  }
  .cover-art {
    position: absolute;
    inset: 0;
    width: 1200px;
    height: 1200px;
  }
  .title-main {
    font-family: "Abril Fatface", serif;
  }
  .title-script, .with-script {
    font-family: "Mrs Saint Delafield", cursive;
  }
  .host-name {
    position: absolute;
    left: 484px;
    top: 905px;
    margin: 0;
    font-family: "Oswald", sans-serif;
    font-weight: 700;
    font-size: 132px;
    line-height: 1;
    letter-spacing: 0;
    color: var(--ink);
    white-space: nowrap;
  }
  .host-portrait {
    position: absolute;
    left: 129px;
    top: 811px;
    width: 256px;
    height: 256px;
    border-radius: 50%;
    border: 7px solid var(--accent-red);
    background: radial-gradient(circle at 50% 45%, #8a7a6c 0%, #4a4038 35%, var(--portrait-base) 75%, #9aa894 100%);
    box-sizing: content-box;
    margin: -7px;
  }
</style>
</head>
<body>
<main class="cover">
  <svg class="cover-art" viewBox="0 0 1200 1200" xmlns="http://www.w3.org/2000/svg" aria-labelledby="cover-title">
    <title id="cover-title">Open Window with Marnie Cole</title>
    <defs>
      <radialGradient id="stage-glow" cx="0.5" cy="0.5" r="0.55">
        <stop offset="0" stop-color="var(--glow)"/>
        <stop offset="0.6" stop-color="#111111"/>
        <stop offset="1" stop-color="var(--ink)"/>
      </radialGradient>
      <linearGradient id="silver" x1="0" y1="0" x2="0" y2="1">
        <stop offset="0" stop-color="#b8b8b8"/>
        <stop offset="0.22" stop-color="var(--silver-light)"/>
        <stop offset="0.5" stop-color="var(--silver-light)"/>
        <stop offset="0.56" stop-color="var(--silver-dark)"/>
        <stop offset="0.8" stop-color="var(--silver-mid)"/>
        <stop offset="1" stop-color="#b0b0b0"/>
      </linearGradient>
    </defs>

    <!-- dark upper field -->
    <rect class="stage" x="0" y="0" width="1200" height="800" fill="url(#stage-glow)"/>

    <!-- torn paper lower field -->
    <path class="torn-edge" fill="var(--paper)"
      d="M0 744 L40 738 L80 742 L120 731 L160 736 L205 726 L240 734 L270 727 L310 738 L350 733 L390 722 L420 728 L460 717 L500 722 L530 712 L565 718 L600 708 L635 712 L665 722 L690 734 L720 742 L750 738 L780 748 L810 744 L835 766 L860 778 L885 772 L915 780 L945 772 L980 762 L1010 756 L1040 760 L1070 754 L1100 760 L1125 751 L1150 756 L1175 746 L1200 752 L1200 1200 L0 1200 Z"/>

    <!-- headline -->
    <text class="title-main" x="184" y="456" font-size="500" textLength="832" lengthAdjust="spacingAndGlyphs" fill="url(#silver)">OPEN</text>

    <text class="title-script" x="255" y="640" font-size="300" textLength="690" lengthAdjust="spacingAndGlyphs" stroke="var(--ink)" stroke-width="3" paint-order="stroke">
      <tspan fill="var(--paper)">Wi</tspan><tspan fill="var(--accent-red)">ndow</tspan>
    </text>

    <text class="with-script" x="500" y="880" font-size="170" fill="var(--accent-red)">with</text>
  </svg>

  <div class="host-portrait" role="img" aria-label="Circular portrait photo of host Marnie Cole"></div>
  <h1 class="host-name">Marnie Cole</h1>
</main>
</body>
</html>
```